FinTech company looking to revamp and expand client-facing interface for our financial models

Pellworth Engines currently has a very simple website that allows clients to interact with our financial models. We are looking to completely redesign the current site and add several extra pages to provide extra functionality. We want the design to have a modern, slick feel, that will work on both a desktop or a tablet. It should be straightforward for clients to move between different pages at any time, and clear from the layout how to interact with the more advanced features. We have included screenshots of existing pages in the attached design brief, as well as sketches of the functionality required by the new pages, but can't provide a direct link to the current site.
Target Market(s)
Professional investors that will be paying to access the interface
Industry/Entity Type
Finance
Number of Pages Required
4 page
Colors
Designer to choose colors to be used in the design.
Look and feel
Each slider illustrates characteristics of the customer's brand and the style your logo design should communicate.

```html
<!DOCTYPE html>
<html lang="en">
<head>
<meta charset="utf-8">
<title>QLENS · Pellworth Engines Models</title>
<link href="https://fonts.googleapis.com/css2?family=Open+Sans:wght@400;600;700&family=Roboto+Condensed:wght@400&display=swap" rel="stylesheet">
<style>
  :root {
    --page-bg: #e6e6e6;
    --panel: #ffffff;
    --bar: #b3b3b3;
    --bar-active: #333333;
    --bar-divider: #c4c4c4;
    --text: #111111;
    --muted: #555555;
    --navy: #00305f;
    --head-grey: #9a9a9a;
    --row-alt: #f4f4f4;
    --grid-line: #e2e2e2;
    --tab-bg: #e4e4e4;
    --accent-blue: #1f4f9c;
  }
  * { box-sizing: border-box; margin: 0; padding: 0; }
  html, body { width: 1200px; height: 752px; overflow: hidden; }
  body { background: var(--page-bg); font-family: "Open Sans", Arial, sans-serif; color: var(--text); position: relative; }

  .app { position: absolute; left: 14px; top: 14px; width: 1172px; height: 724px; background: var(--panel); overflow: hidden; }

  .topbar { position: absolute; left: 0; top: 0; width: 100%; height: 55px; background: var(--bar); display: flex; }
  .brand { width: 166px; padding-left: 53px; line-height: 55px; font-weight: 700; font-size: 17px; }
  .range-tab, .nav-tab { height: 55px; display: flex; align-items: center; justify-content: center; font-weight: 700; font-size: 13px; border-right: 1px solid var(--bar-divider); gap: 8px; }
  .range-tab { width: 84px; }
  .range-tab.is-active, .nav-tab.is-active { background: var(--bar-active); color: #fff; }
  .range-tab:nth-child(3) { width: 85px; }
  .range-tab:nth-child(4) { width: 83px; }
  .spacer { flex: 1; border-right: 1px solid var(--bar-divider); }
  .nav-tab { width: 130px; }
  .nav-tab.wide { width: 164px; }
  .nav-tab.last { width: 181px; border-right: 0; }
  .nav-tab svg { width: 20px; height: 20px; }

  .subnav { position: absolute; left: 0; top: 55px; width: 100%; height: 93px; background: linear-gradient(#fbfbfb, #d6d6d6); }
  .sub-tab { position: absolute; top: 42px; width: 143px; height: 51px; background: linear-gradient(#ececec, #e0e0e0); border-radius: 4px 4px 0 0; display: flex; flex-direction: column; align-items: center; justify-content: flex-end; padding-bottom: 6px; gap: 4px; font-size: 12px; color: #555; }
  .sub-tab svg { width: 18px; height: 18px; }

  .filters { position: absolute; left: 53px; top: 184px; font-size: 15px; }
  .filter-row { display: flex; align-items: center; height: 29px; margin-bottom: 8px; }
  .filter-name { width: 80px; }
  .filter-label { width: 93px; font-weight: 700; }
  .filter-input { width: 167px; height: 29px; border: 1px solid #cfcfcf; border-radius: 4px; padding: 4px 10px; font-size: 15px; font-family: inherit; line-height: 19px; }

  .export { position: absolute; left: 1038px; top: 226px; display: flex; align-items: center; gap: 7px; color: var(--accent-blue); font-weight: 700; font-size: 15px; }
  .export svg { width: 24px; height: 22px; }

  .models-table { position: absolute; left: 51px; top: 277px; width: 1070px; border-collapse: separate; border-spacing: 0; table-layout: fixed; border-radius: 6px; overflow: hidden; box-shadow: 0 2px 8px rgba(0,0,0,0.14); background: #fff; font-family: "Roboto Condensed", Arial, sans-serif; font-size: 15px; }
  .models-table th { height: 65px; color: #fff; font-family: "Open Sans", Arial, sans-serif; font-weight: 600; font-size: 15.5px; background: var(--head-grey); border-right: 1px solid #ababab; }
  .models-table th.key { background: var(--navy); border-right: 1px solid #1c4775; }
  .models-table th:last-child { border-right: 0; }
  .models-table td { height: 64px; padding: 0 8px; border-right: 1px solid var(--grid-line); border-top: 1px solid var(--grid-line); line-height: 19px; }
  .models-table td:last-child { border-right: 0; }
  .models-table tbody tr:nth-child(even) td { background: var(--row-alt); }
  .models-table td.id { text-align: center; }
</style>
</head>
<body>
<div class="app">
  <header class="topbar">
    <div class="brand">QLENS</div>
    <div class="range-tab is-active">250D</div>
    <div class="range-tab">83D</div>
    <div class="range-tab">42D</div>
    <div class="spacer"></div>
    <div class="nav-tab is-active">
      <svg viewBox="0 0 20 20" fill="none" stroke="#fff" stroke-width="1.8"><path d="M2 10 L10 3 L18 10"/><path d="M4.5 8.5 V17 H8.5 V12 H11.5 V17 H15.5 V8.5"/></svg>MODELS</div>
    <div class="nav-tab wide">
      <svg viewBox="0 0 20 20" fill="#222"><circle cx="10" cy="10" r="2"/><circle cx="10" cy="3" r="1.3"/><circle cx="10" cy="17" r="1.3"/><circle cx="3" cy="10" r="1.3"/><circle cx="17" cy="10" r="1.3"/><circle cx="5" cy="5" r="1.3"/><circle cx="15" cy="5" r="1.3"/><circle cx="5" cy="15" r="1.3"/><circle cx="15" cy="15" r="1.3"/><circle cx="10" cy="6.5" r="1"/><circle cx="10" cy="13.5" r="1"/><circle cx="6.5" cy="10" r="1"/><circle cx="13.5" cy="10" r="1"/></svg>SENSITIVITIES</div>
    <div class="nav-tab last">
      <svg viewBox="0 0 20 20" fill="none" stroke="#222" stroke-width="1.6"><path d="M10 1.8 L12.4 7.3 L18.3 7.7 L13.8 11.6 L15.2 17.5 L10 14.3 L4.8 17.5 L6.2 11.6 L1.7 7.7 L7.6 7.3 Z"/></svg>FAVOURITES</div>
  </header>

  <nav class="subnav">
    <div class="sub-tab" style="left:219px">
      <svg viewBox="0 0 18 18" fill="#555"><rect x="2" y="3" width="14" height="2"/><rect x="2" y="8" width="10" height="2"/><rect x="13" y="8" width="3" height="2"/><rect x="2" y="13" width="14" height="2"/></svg>EQUITIES</div>
    <div class="sub-tab" style="left:367px">
      <svg viewBox="0 0 18 18" fill="#555"><rect x="2" y="11" width="3" height="6"/><rect x="7" y="8" width="3" height="9"/><rect x="12" y="5" width="3" height="12"/><path d="M2 8 L7 4 L10 6 L15 1" stroke="#555" stroke-width="1.4" fill="none"/></svg>ETFS</div>
    <div class="sub-tab" style="left:515px">
      <svg viewBox="0 0 18 18" fill="none" stroke="#555" stroke-width="1.6"><circle cx="8" cy="10" r="6.5"/><circle cx="8" cy="10" r="2.5"/><path d="M8 10 L15 3"/></svg>PAIRS</div>
    <div class="sub-tab" style="left:663px">
      <svg viewBox="0 0 18 18" fill="none" stroke="#555" stroke-width="1.5"><rect x="3" y="1.5" width="12" height="15" rx="1.5"/><path d="M6 6 H12 M6 9 H12 M6 12 H12"/></svg>ETF PAIRS</div>
    <div class="sub-tab" style="left:811px">
      <svg viewBox="0 0 18 18" fill="#555"><path d="M5 3 L13 1 V15 L5 17 Z"/></svg>FACTORS</div>
  </nav>

  <section class="filters">
    <div class="filter-row"><span class="filter-name">Quality</span><span class="filter-label">Threshold:</span><input class="filter-input" value="-10"></div>
    <div class="filter-row"><span class="filter-name"><b>Abs.</b> Stat</span><span class="filter-label">Threshold:</span><input class="filter-input" value="-10"></div>
  </section>

  <div class="export">
    <svg viewBox="0 0 24 22" fill="none" stroke="#1f4f9c" stroke-width="2"><path d="M11 4 H4 A2 2 0 0 0 2 6 V18 A2 2 0 0 0 4 20 H17 A2 2 0 0 0 19 18 V13"/><path d="M8 15 C9 9 13 7 20 7"/><path d="M16 3 L21 7 L16 11"/></svg>Export</div>

  <table class="models-table">
    <colgroup>
      <col style="width:92px"><col style="width:102px"><col style="width:106px"><col style="width:106px">
      <col style="width:83px"><col style="width:83px"><col style="width:83px"><col style="width:83px">
      <col style="width:83px"><col style="width:83px"><col style="width:83px"><col style="width:83px">
    </colgroup>
    <thead>
      <tr>
        <th class="key">ID &#8964;</th><th class="key">Sector</th><th class="key">Time</th>
        <th>Quality</th><th>Stat 1</th><th>Stat 2</th><th>Stat 3</th><th>Stat 4</th><th>Stat 5</th><th>Stat 6</th><th>Stat 7</th><th>Stat 8</th>
      </tr>
    </thead>
    <tbody>
      <tr><td class="id">Model 1</td><td>Materials</td><td>2019-07-03<br>12:15:00.000</td><td>30.2288</td><td>2.01574</td><td>23.305</td><td>-0.149368</td><td>22.3054</td><td>4.63714</td><td>0.945706</td><td>2.81949</td><td>2.60858</td></tr>
      <tr><td class="id">Model 2</td><td>Industrials</td><td>2019-07-03<br>12:15:00.000</td><td>32.8694</td><td>0.87307</td><td>32.185</td><td>-0.033692</td><td>33.9911</td><td>11.5693</td><td>-0.472968</td><td>-0.830458</td><td>6.80646</td></tr>
      <tr><td class="id">Model 3</td><td>Consumer<br>Discretionary</td><td>2019-07-03<br>12:15:00.000</td><td>1.66002</td><td>-0.569222</td><td>159.814</td><td>0.0252328</td><td>172.616</td><td>10.2875</td><td>-0.750396</td><td>-0.385309</td><td>4.69146</td></tr>
      <tr><td class="id">Model 4</td><td>Information<br>Technology</td><td>2019-07-03<br>12:15:00.000</td><td>45.6856</td><td>0.412148</td><td>202.488</td><td>0.0084923</td><td>205.834</td><td>11.9094</td><td>-0.137913</td><td>0.449595</td><td>3.85106</td></tr>
      <tr><td class="id">Model 5</td><td>Information<br>Technology</td><td>2019-07-03<br>12:15:00.000</td><td>75.7733</td><td>7.06728</td><td>188.605</td><td>0.016913</td><td>161.665</td><td>3.82241</td><td>0.981019</td><td>1.29847</td><td>3.34927</td></tr>
    </tbody>
  </table>
</div>
</body>
</html>
```